TA BRAMLEY BUSINESS CARD DESIGN PROJECT

We need to utilize our logo that was expertly created on PixelHarbor and now need to match this with a business card design.

```html
<!DOCTYPE html>
<html lang="en">
<head>
<meta charset="utf-8">
<title>TA BRAMLEY Business Card</title>
<link rel="stylesheet" href="https://fonts.googleapis.com/css2?family=Montserrat:wght@400;500;700&display=swap">
<style>
  :root {
    --brand-blue: #0e57a8;
    --card-black: #1a1a1a;
    --card-white: #ffffff;
    --page-bg: #dcdcda;
    --text-light: #f2f2f2;
  }
  * { margin: 0; padding: 0; box-sizing: border-box; }
  html, body { width: 1200px; height: 801px; overflow: hidden; }
  body {
    background: var(--page-bg);
    font-family: "Montserrat", sans-serif;
    position: relative;
  }
  .card {
    position: absolute;
    top: 246px;
    width: 540px;
    height: 309px;
    overflow: hidden;
    box-shadow: 0 6px 18px rgba(0,0,0,0.18);
  }
  .card-front { left: 40px; background: var(--card-white); }
  .card-back { left: 620px; background: var(--brand-blue); }

  .front-wave { position: absolute; inset: 0; width: 100%; height: 100%; }

  .wordmark {
    position: absolute;
    display: flex;
    align-items: center;
    gap: 10px;
    font-weight: 700;
    letter-spacing: 0.14em;
    white-space: nowrap;
  }
  .wordmark-square { display: block; flex: none; }
  .card-front .wordmark {
    left: 34px; top: 134px;
    font-size: 26px;
    color: var(--brand-blue);
  }
  .card-front .wordmark-square { width: 22px; height: 22px; background: var(--brand-blue); }
  .card-back .wordmark {
    left: 50%; top: 50%;
    transform: translate(-50%, -50%);
    font-size: 50px;
    color: var(--card-white);
  }
  .card-back .wordmark-square { width: 40px; height: 40px; background: var(--card-white); }

  .accent-tab {
    position: absolute;
    right: 0; top: 26px;
    width: 34px; height: 26px;
    background: var(--brand-blue);
  }
  .contact {
    position: absolute;
    right: 48px; top: 26px;
    text-align: right;
    color: var(--text-light);
  }
  .contact-name {
    font-size: 17px; font-weight: 700;
    color: var(--brand-blue);
    letter-spacing: 0.03em;
    line-height: 26px;
  }
  .contact-role { font-size: 11.5px; font-weight: 400; margin-bottom: 26px; }
  .contact-list { list-style: none; font-size: 11.5px; line-height: 20px; }
  .contact-list li { display: flex; justify-content: flex-end; align-items: center; gap: 8px; }
  .contact-list svg { width: 11px; height: 11px; fill: var(--brand-blue); margin-right: -20px; }
  .contact-address { font-size: 11.5px; line-height: 17px; margin-top: 22px; }
</style>
</head>
<body>
  <section class="card card-front" aria-label="Business card front">
    <svg class="front-wave" viewBox="0 0 540 309" aria-hidden="true">
      <path d="M250 0 C330 8 300 120 300 170 C300 240 330 290 385 309 L540 309 L540 0 Z" fill="var(--card-black)"/>
      <path d="M252 6 C312 20 286 120 288 170 C290 240 315 285 360 305 C322 282 300 240 300 170 C300 120 318 20 252 6 Z" fill="var(--brand-blue)"/>
    </svg>
    <div class="wordmark"><span class="wordmark-square"></span>TA BRAMLEY</div>
    <div class="accent-tab"></div>
    <div class="contact">
      <p class="contact-name">MARCUS HALE</p>
      <p class="contact-role">Managing Director</p>
      <ul class="contact-list">
        <li>123 456 789<svg viewBox="0 0 12 12"><path d="M3 1l2 2.5-1.2 1.3a7 7 0 0 0 3.4 3.4L8.5 7 11 9l-1.5 2C5 11 1 7 1 2.5z"/></svg></li>
        <li>info@yourmail.com<svg viewBox="0 0 12 12"><path d="M1 2.5h10v7H1z M1 2.5l5 4 5-4"/></svg></li>
        <li>www.yourwebsite.com<svg viewBox="0 0 12 12"><circle cx="6" cy="6" r="5"/></svg></li>
      </ul>
      <p class="contact-address">Your address, City<br>State, Zip 1234</p>
    </div>
  </section>

  <section class="card card-back" aria-label="Business card back">
    <div class="wordmark"><span class="wordmark-square"></span>TA BRAMLEY</div>
  </section>
</body>
</html>
```